KVT Web Design Project

I would like a simple and elegant design for my international business consulting practice web site. I already have new KVT Logo and will have brochure-colors are blue, green and black

Practice areas:
I offer consulting services specializing in developing Internet-based anti-counterfeiting and anti-fraud programs, test purchases and investigations.

I offer Cyber Security, Data Protection and Compliance services

I also offer International Due Diligence Investigations and Country and Travel Risk Assessments

General Background Investigations

Physical Security Services

About me section listing my Bio

I have a set of key associates that I work with around the world and will want to list their CVs or Bios under "KVT

Associates"Banner with nice photo but not too cluttered

Ability to Upload documents and articles

Contact us section
Updates

I have uploaded my new logo-please advise if you didn't get it or it is not in the correct file format.

Thank you

Dominic

Hello Everyone,

Thank you for your submissions and ideas. I'm not sure about design only vs code. I understand that some of you do not do code-if not then please just provide design.

More about my business: see below link on Google docs to my brochure-this should help but don't use that phone number-see below.

https://files.quillbin.example/view?id=7Qx2Lm9Pz4Rt8Kw3Hn6Vb1Jc5Fd0Sg

 

Here are some details.

Contacts:

Dominic R. Torvello, CPP

President

Torvello and Associates, LLC

P.O. Box 47129

Gaithersburg, MD 20914

USA

web address:www.Torvelloandassociates.example (currently not working)

email:dom @torvelloand associates.example

Tel: 202-555-0173

I hope this is helpful. Dom

Reason: Sorry but during holiday period, have not had as much time to devote to this project. Thanks for your submissions.

Per my previous guidance, please keep designs simple and elegant and free from traditional security images with locks and chains-I prefer one or at most, two photos. Two colors- blue and green in addition to black for print. I want to present professional, corporate and international image. Thank you for your ideas nad submissions.

Dom

Target Market(s)

Law firms, large multi-national corporations, Security Industry

Industry/Entity Type

Business

Requirements
Must have
• Must have sections: (will provide text)

About KVT (will provide text)

Practice areas

Associates (will provide text)

Contact us

(it must also have ability to upload files and articles)
Should not have
• Old style fonts and symbols such as security badges, scales of justice, etc. I want a sleek and modern design.

```html
<!DOCTYPE html>
<html lang="en">
<head>
<meta charset="utf-8">
<title>Torvello &amp; Associates, LLC — Business Consulting</title>
<link rel="stylesheet" href="https://fonts.googleapis.com/css2?family=Ubuntu:wght@400;500&family=Roboto+Condensed:wght@400;700&family=Arimo:wght@400;700&display=swap">
<style>
:root{
  --page:#d0d0d0;
  --ink:#1e1e1e;
  --brand:#1f5fa8;
  --brand-light:#3d8fcf;
  --hero-top:#5b8fc9;
  --hero-bottom:#6e9fd3;
  --footer-top:#0b3c80;
  --footer-bottom:#072e66;
  --accent:#e08a1a;
  --link:#3d9ad6;
  --footer-text:#d8e4f4;
}
*{box-sizing:border-box;margin:0;padding:0}
html,body{width:1114px;height:1200px;overflow:hidden;background:var(--page);font-family:"Arimo",Arial,sans-serif;color:var(--ink)}
.canvas{position:relative;width:1114px;height:1200px}
.abs{position:absolute}
.social{display:flex;gap:5px}
.social span{display:block;width:22px;height:22px;border-radius:3px}
.social .s1{background:#6f6f6f}.social .s2{background:#2f6bc4}.social .s3{background:#1f7fc1}.social .s4{background:#e8741c}
.social.small span{width:20px;height:20px}
.top-social{left:836px;top:30px}

.header{left:146px;top:62px;width:822px;height:96px;background:linear-gradient(#f7f8fa,#e9ecf0);border-radius:4px 4px 0 0}
.wordmark{display:flex;align-items:center;font-family:"Ubuntu",sans-serif;font-weight:400;color:#222;white-space:nowrap}
.wordmark .square{display:block;width:28px;height:28px;background:var(--brand);margin-right:12px}
.wordmark .name{font-size:26px}
.header .wordmark{position:absolute;left:24px;top:23px}
.tagline{position:absolute;left:124px;top:61px;font-family:"Ubuntu",sans-serif;font-size:17px;letter-spacing:2.2px;color:var(--brand);white-space:nowrap}
.service-line{position:absolute;left:611px;top:32px;font-family:"Ubuntu",sans-serif;font-size:18.5px;color:var(--brand-light);white-space:nowrap}
.search{position:absolute;left:676px;top:61px;width:122px;height:22px;border:1px solid #aaa;border-radius:11px;background:#fbfbfb;font-size:9px;color:#555;padding:5px 10px}
.search b{position:absolute;right:3px;top:3px;width:22px;height:14px;border-radius:7px;background:#444;color:#fff;font-size:8px;text-align:center;line-height:14px;font-weight:400}

.nav{left:146px;top:158px;width:822px;height:48px;background:linear-gradient(#f0f0f0,#d6d6d6);display:flex;align-items:center;padding:6px 0 0 19px;font-size:10.5px;font-weight:700;color:#222;white-space:nowrap}
.nav span.sep{margin:0 12px;font-weight:400}

.hero{left:146px;top:206px;width:822px;height:286px;background:linear-gradient(var(--hero-top),var(--hero-bottom));border-bottom:1px solid #2b4f80}
.hero h1{position:absolute;left:29px;top:55px;font-family:"Roboto Condensed",sans-serif;font-weight:400;font-size:26.5px;color:#fff;white-space:nowrap}
.hero p{position:absolute;left:24px;top:113px;font-size:14px;line-height:21px;letter-spacing:-0.3px;color:#f2f6fb;white-space:nowrap}
.btn{position:absolute;top:228px;height:33px;border-radius:4px;color:#fff;font-family:"Roboto Condensed",sans-serif;font-size:13.5px;text-align:center;line-height:33px}
.btn-primary{left:26px;width:119px;background:linear-gradient(#f4a83a,#d97f0f)}
.btn-secondary{left:172px;width:136px;background:linear-gradient(#4f9cc4,#2f7aa6)}
.hero-frame{position:absolute;left:353px;top:29px;width:443px;height:231px;background:#2b2b2b;padding:13px}
.hero-photo{width:417px;height:205px;background:linear-gradient(120deg,#123a8a,#2c66c0 40%,#3c5a80 70%,#0d1a30)}

.services{left:146px;top:492px;width:822px;height:272px;background:linear-gradient(#dcdcdc,#e8e8e8 20%);border-bottom:1px solid #9a9a9a}
.service{position:absolute;top:22px}
.service .icon{position:absolute;border-radius:6px}
.service h2{position:absolute;top:31px;font-family:"Roboto Condensed",sans-serif;font-weight:400;font-size:16px;white-space:nowrap;color:#222}
.service p{position:absolute;top:69px;font-family:"Roboto Condensed",sans-serif;font-size:11.5px;letter-spacing:-0.35px;line-height:14.5px;color:#333;white-space:nowrap}
.service a{color:var(--link);text-decoration:none}
.divider{position:absolute;top:24px;width:1px;height:200px;background:#cfcfcf}

.footer{left:146px;top:773px;width:822px;height:290px;background:linear-gradient(var(--footer-top),var(--footer-bottom));border-radius:0 0 6px 6px}
.col{position:absolute;top:24px;width:156px;font-family:"Roboto Condensed",sans-serif;white-space:nowrap}
.col h3{font-weight:400;font-size:13px;color:#fff;padding-bottom:3px;border-bottom:1px solid #b07a3a}
.col .body{margin-top:22px;font-size:9.5px;line-height:12px;color:var(--footer-text)}
.date{color:var(--accent);font-size:9.5px}
.item-title{color:#fff;font-weight:700;font-size:12px}
.entry{margin-bottom:11px}
.entry .title-line{display:block;margin-bottom:2px;line-height:15px}
.tweet{font-size:12px;line-height:14.5px;color:#fff;margin-bottom:7px}
.tweet.gap{margin-bottom:11px}
.col .text{font-size:11px;line-height:14.4px;color:var(--footer-text);margin-top:20px}
.col .text a{color:var(--link);text-decoration:none}
.col .text .warm{color:var(--accent)}
.footer-rule{position:absolute;left:150px;top:252px;width:640px;height:1px;background:linear-gradient(90deg,transparent,#4f74a8)}
.footer .social{position:absolute;left:699px;top:245px}
.copyright{position:absolute;left:312px;top:264px;font-size:10px;color:#dfe8f5;white-space:nowrap}

.bottom-nav{left:0;top:1085px;width:1114px;display:flex;justify-content:center;font-size:9.5px;font-weight:700;color:#222;white-space:nowrap}
.bottom-nav span.sep{margin:0 11px;font-weight:400}
.bottom-mark{left:436px;top:1118px}
.bottom-mark .square{width:18px;height:18px;margin-right:8px}
.bottom-mark .name{font-size:17px}
</style>
</head>
<body>
<div class="canvas">
  <div class="abs social top-social" aria-label="Social links"><span class="s1"></span><span class="s2"></span><span class="s3"></span><span class="s4"></span></div>

  <header class="abs header">
    <div class="wordmark"><span class="square"></span><span class="name">Torvello &amp; Associates, LLC</span></div>
    <div class="tagline">Intellectual Property and Cyber Security</div>
    <div class="service-line">Business Consulting</div>
    <div class="search">Search...<b>GO</b></div>
  </header>

  <nav class="abs nav">
    <span>HOME</span><span class="sep">I</span><span>ABOUT KVT</span><span class="sep">I</span><span>PRACTICE AREAS</span><span class="sep">I</span><span>ASSOCIATES</span><span class="sep">I</span><span>CONTACT US</span>
  </nav>

  <section class="abs hero">
    <h1>Cyber Security</h1>
    <p>Lorem ipsum dolor sit amet, consectetur adipte<br>scing elit. Sed hendrerit ante et lorem tempus<br>ac semper enim porttitor.</p>
    <div class="btn btn-primary">WHAT WE DO</div>
    <div class="btn btn-secondary">VIEW PORTFOLIO</div>
    <div class="hero-frame"><div class="hero-photo" role="img" aria-label="Photo of analysts working at a bank of monitoring screens"></div></div>
  </section>

  <section class="abs services">
    <div class="service" style="left:54px">
      <div class="icon" style="left:0;top:8px;width:52px;height:52px;border-radius:26px;background:radial-gradient(circle at 35% 35%,#6fa8e0,#1c4f92)" role="img" aria-label="Globe with shield icon"></div>
      <h2 style="left:57px">CYBER SECURITY</h2>
      <p style="left:-2px">Donec mattis nulla sit amet sem pharetra<br>euismod. Pellentesque vel tortor ac mi iaculis<br>tempor. Praesent dui sapien, facilisis a lobortis<br>nec, adipiscing id tellus. Proin facilisis ultricies<br>purus et eleifend. Vestibulum consectetur<br>aliquam viverra. Aliquam rhoncus velit non<br>metus varius pretium.&nbsp; <a>Learn More...</a></p>
    </div>
    <div class="divider" style="left:273px"></div>
    <div class="service" style="left:286px">
      <div class="icon" style="left:0;top:1px;width:60px;height:60px;background:linear-gradient(#9cc4ea,#4f86c0)" role="img" aria-label="Magnifying glass icon"></div>
      <h2 style="left:65px">GENERAL INVESTIGATIONS</h2>
      <p style="left:14px">Vivamus nec dolor mattis lectus scelerisque phare-<br>tra. Sed ac tortor vel ante egestas congue. Sed vitae<br>tellus vel mi rhoncus mollis quis eu velit. Cras adipi-<br>scing erat mi. Integer dapibus urna eu sem volutpat<br>sit amet sodales libero varius. Cras adipiscing erat<br>mi. Integer dapibus urna eu sem.<br><a>Learn More...</a></p>
    </div>
    <div class="divider" style="left:548px"></div>
    <div class="service" style="left:561px">
      <div class="icon" style="left:0;top:1px;width:54px;height:60px;background:linear-gradient(#5e7f9e,#1f3a56)" role="img" aria-label="Monitor with gear icon"></div>
      <h2 style="left:60px">DATA PROTECTION</h2>
      <p style="left:13px">Maecenas vitae leo metus. Integer lacinia leo<br>urna, nec elementum lectus. Suspendisse<br>turpis justo, rhoncus quis sagittis vel, sceleris-<br>que quis felis. Maecenas eu quam at felis<br>posuere lacinia et pellentesque augue. Donec<br>vitae ligula eget nulla interdum laoreet a sollici-<br>tudin ligula.<br><a>Learn More...</a></p>
    </div>
  </section>

  <footer class="abs footer">
    <div class="col" style="left:53px">
      <h3>RECENT PROJECTS</h3>
      <div class="body">
        <div class="entry"><span class="title-line"><span class="date">12.07.09</span>&nbsp; <span class="item-title">Project Name</span></span>Aliquam eget est eget sem semper<br>accumsan id a dolor. Etiam scelerique mi<br>id arcu euismod pretium vulputate elit<br>rhoncus.</div>
        <div class="entry"><span class="title-line"><span class="date">03.07.09</span>&nbsp; <span class="item-title">Another Project</span></span>Aliquam eget est eget sem semper<br>accumsan id a dolor. Etiam scelerique mi<br>id arcu euismod pretium vulputate.</div>
      </div>
    </div>
    <div class="col" style="left:240px">
      <h3>FEED</h3>
      <div class="body">
        <div class="tweet"><span class="date">12.07.09</span>&nbsp; I have just redesign my<br>&nbsp;website...</div>
        <div class="tweet gap"><span class="date">11.07.09</span> Morbi sem mauris, lobort<br>iset faucibus ac, semper id tortor.</div>
        <div class="tweet"><span class="date">06.07.09</span>&nbsp; Integer vitae maa turpis.<br>&nbsp;Nullased nunc arcu...</div>
        <div class="tweet"><span class="date">06.07.09</span>&nbsp; Integer vitae maa turpis.<br>&nbsp;Nullased nunc arcu...</div>
      </div>
    </div>
    <div class="col" style="left:430px">
      <h3>ABOUT US</h3>
      <div class="text">We are Lorem ipsum dolor sit<br>amet, consectetur adipiscing elit.<br>Nullam ligula massa, egestas ut<br>pellentesque non, luctus nec diam.<br>Cum sociis natoque penatibus et<br>magnis dis parturient montes,<br>nascetur ridiculus mus. Suspend-<br>isse at quam eget ante pellen-<br>tesque dapibus vel nec <span class="warm">tortor.</span></div>
    </div>
    <div class="col" style="left:620px">
      <h3>CONTACTS</h3>
      <div class="text">If you have a new idea to tell us, or<br>just need to hear a friendly voice<br>feel free to <a>contact us</a> anytime.</div>
    </div>
    <div class="footer-rule"></div>
    <div class="social small"><span class="s1"></span><span class="s2"></span><span class="s3"></span><span class="s4"></span></div>
    <div class="copyright">© 2011, torvelloandassociates.example</div>
  </footer>

  <nav class="abs bottom-nav">
    <span>HOME</span><span class="sep">I</span><span>ABOUT KVT</span><span class="sep">I</span><span>PRACTICE AREAS</span><span class="sep">I</span><span>ASSOCIATES</span><span class="sep">I</span><span>CONTACT US</span>
  </nav>

  <div class="abs wordmark bottom-mark"><span class="square"></span><span class="name">Torvello &amp; Associates, LLC</span></div>
</div>
</body>
</html>
```